Flat bootstrap design for existing site

I'm looking for a modern flat design based around an existing logo. This has to be a custom design (no external templates), and implemented into a bootstrap framework.

The logo is attached as 2 versions - choose whichever you want, that flows better with whatever design you choose.

Added screenshots of the existing site (currently using the default bootstrap layouts). Please make your designs around those pages in the screenshots (i.e. the homepage only has the postal code input and the header). The active page has 3 screenshots, because I wanted to illustrate the other states that would be visible (in the table rows).

This is a moving/junk removal website, just for some context.

Here's some example websites (flat designs) that I like, just to give you an idea of what I'm after.

https://www.plimvora.com/
https://dacklow.com/
https://trevanu.com/
https://quobrintal.com/en/

Coding

Coded - Design and coding required

Number of Pages Required

5+ page

Colors

Designer to choose colors to be used in the design.

Requirements
Must have
• It must be a modern/simple flat design, that is built around the existing logo (attached).
• It has to be implemented using bootstrap.

```html
<!DOCTYPE html>
<html lang="en">
<head>
<meta charset="utf-8">
<title>Haultro – Junk Removal</title>
<link rel="stylesheet" href="https://fonts.googleapis.com/css2?family=Montserrat:wght@400;500;600&display=swap">
<style>
  :root {
    --brand: #48c8f1;
    --ink: #1c1c1c;
    --paper: #fbf9f5;
    --field-border: #e3e1dc;
    --muted: #a3a3a3;
    --skyline: #e6e2dd;
    --skyline-deep: #dcd8d3;
    --ground: #bfbfc7;
    --bin: #7fd6d0;
    --footer-ink: #3a3a3a;
    --icon: #8e8e8e;
  }
  * { box-sizing: border-box; margin: 0; padding: 0; }
  html, body { width: 1200px; height: 658px; overflow: hidden; }
  body {
    background: var(--paper);
    font-family: "Montserrat", sans-serif;
    color: var(--ink);
    position: relative;
    border-top: 3px solid var(--brand);
  }
  .brand {
    position: absolute; left: 99px; top: 32px;
    display: flex; align-items: center; gap: 10px;
    font-size: 38px; font-weight: 600; line-height: 48px; color: var(--brand);
    letter-spacing: 1px;
  }
  .brand-dot { width: 20px; height: 20px; border-radius: 50%; background: var(--brand); }
  .nav-link {
    position: absolute; top: 30px; height: 37px;
    font-size: 13px; font-weight: 500; color: var(--ink);
    text-decoration: none; line-height: 37px; white-space: nowrap;
  }
  .nav-link.is-active { color: var(--brand); left: 627px; }
  .nav-link.how { left: 696px; }
  .nav-link.driver {
    left: 813px; width: 152px; text-align: center;
    background: var(--brand); color: #fff; border-radius: 2px;
  }
  .nav-link.signin { left: 981px; }
  .hero-title {
    position: absolute; top: 220px; left: 0; width: 1200px; text-align: center;
    font-size: 33px; line-height: 44px; font-weight: 500; letter-spacing: 0.3px;
  }
  .hero-title .accent { color: var(--brand); }
  .hero-title strong { font-weight: 600; }
  .booking-form { position: absolute; top: 295px; left: 339px; display: flex; gap: 12px; }
  .postal-input {
    width: 288px; height: 41px; border: 1px solid var(--field-border); background: #fff;
    font-family: inherit; font-size: 12px; font-weight: 500; padding-left: 19px; color: var(--ink);
  }
  .postal-input::placeholder { color: var(--muted); }
  .book-button {
    width: 150px; height: 41px; border: 0; border-radius: 2px;
    background: var(--brand); color: #fff; font-family: inherit; font-size: 17px; font-weight: 500;
  }
  .city-scene { position: absolute; left: 119px; top: 334px; width: 952px; height: 262px; }
  .bin-scene { position: absolute; left: 345px; top: 383px; width: 500px; height: 206px; }
  .social-links { position: absolute; left: 104px; top: 623px; display: flex; gap: 23px; }
  .social-links span { width: 10px; height: 10px; border-radius: 50%; background: var(--icon); display: block; }
  .copyright {
    position: absolute; right: 126px; top: 620px;
    font-size: 11px; line-height: 16px; color: var(--footer-ink);
  }
</style>
</head>
<body>
  <header>
    <div class="brand"><span class="brand-dot"></span>HAULTRO</div>
    <nav class="main-nav">
      <a class="nav-link is-active" href="#">BOOK</a>
      <a class="nav-link how" href="#">HOW IT WORKS</a>
      <a class="nav-link driver" href="#">BECOME A DRIVER</a>
      <a class="nav-link signin" href="#">SIGN IN</a>
    </nav>
  </header>

  <main>
    <h1 class="hero-title">NEED <span class="accent">JUNK REMOVED?</span> <strong>BOOK NOW.</strong></h1>
    <form class="booking-form">
      <input class="postal-input" type="text" placeholder="Postal Code">
      <button class="book-button" type="button">BOOK</button>
    </form>

    <svg class="city-scene" viewBox="0 0 952 262" role="img" aria-label="Faint city skyline illustration">
      <defs>
        <linearGradient id="skyFade" x1="0" y1="0" x2="0" y2="1">
          <stop offset="0" stop-color="var(--skyline)" stop-opacity="0.15"/>
          <stop offset="1" stop-color="var(--skyline-deep)" stop-opacity="0.9"/>
        </linearGradient>
      </defs>
      <rect x="0" y="20" width="952" height="235" fill="url(#skyFade)"/>
      <rect x="0" y="255" width="952" height="5" fill="var(--ground)"/>
    </svg>

    <svg class="bin-scene" viewBox="0 0 500 206" role="img" aria-label="Illustration of an overflowing recycling bin with bottles and litter">
      <defs>
        <radialGradient id="binGlow" cx="0.5" cy="0.55" r="0.5">
          <stop offset="0" stop-color="var(--bin)"/>
          <stop offset="0.55" stop-color="var(--bin)" stop-opacity="0.55"/>
          <stop offset="1" stop-color="var(--bin)" stop-opacity="0"/>
        </radialGradient>
      </defs>
      <ellipse cx="250" cy="110" rx="170" ry="96" fill="url(#binGlow)"/>
    </svg>
  </main>

  <footer>
    <div class="social-links" aria-label="Social links">
      <span></span><span></span><span></span><span></span>
    </div>
    <p class="copyright">Copyrights © 2017 - All Rights Reserved</p>
  </footer>
</body>
</html>
```